Web Design Project - Brunnwald Haus

We would like you to refine our web layouts for a (1) homepage and (2) a product page (see attached files for reference).

The client is a swiss construction company, that designs, builds and sells standardized and tailored-made residential houses.

His logo is old, but not up for redesign. The only way to salvage it, is to incorporate its yellow color (as highlight) to the overall design, so as to create some brand awareness.

REQUIREMENTS FOR THE HOMEPAGE:
1. telephone number over menu
2. logo + menu with 6 categories
3. slider for showing various house types (for pics, see attachments)
4. "AKTUELL" card with yellow color (to show his most actual projects) and a strong Call For Action (what in German would be: KONTAKT AUFNEHMEN)
5. a yellow stripe for his company's slogan (Ihr Partner für individuelle und normierte Wohnbauten)
6. A left coloumn with
(a) two picture-holders under the title REFERENZEN
(b) the three supporting logos of TELV, KALDORIS and VB NULLBAU HELVETIA (can be downloaded as pngs)
7. A right column with 6 headlines + texts of 3 lines each
8. a footer with the adress info

REQUIREMENTS FOR PRODUKT PAGE:
1. slider for pictures
2. info box with Call For Action for particular House-types
3. thumbnail pics under the slider for additional images of any particular house type
4. Left-side: name of house type and picture
5. Right-side: Header and blindtext for house description
6. three placeholders for 3 floor plans
Updates

NB No coding necessary. An imaginative, fresh design along the layout requirements will do.
Thanx to all

To all those who had probs with the downloading of the attached files:
we've posted a new Zip.
Have a look!
thankx

Thanks to everyone who participated.
We will be showing a selection of your designs to the client within the next couple of days.
We'll get back to you, as soon as possible.

Industry/Entity Type

Construction

Requirements
Must have
• - slider
- info box with call for action
- thumbnail pictures
- fresh look based on colors, design of elements (slider, info box), font selection

```html
<!DOCTYPE html>
<html lang="de">
<head>
<meta charset="utf-8">
<title>Brunnwald Haus – Startseite</title>
<link rel="stylesheet" href="https://fonts.googleapis.com/css2?family=Open+Sans:wght@400;600;700;800&display=swap">
<style>
:root{
  --yellow:#f5c400;
  --yellow-dark:#e0a800;
  --ink:#2b2b2b;
  --nav:#3b3b3b;
  --text:#5a5a5a;
  --muted:#8a8a8a;
  --line:#dcdcdc;
  --panel:#f2f2f2;
  --footer:#ececec;
  --white:#ffffff;
}
*{box-sizing:border-box;margin:0;padding:0}
html,body{width:804px;height:1200px;overflow:hidden}
body{background:var(--white);font-family:"Open Sans",Arial,sans-serif;color:var(--text);position:relative;font-size:8px;line-height:1.35}
.page{position:absolute;left:32px;width:746px}

/* header */
.header{top:10px;height:46px}
.brand{position:absolute;left:0;top:6px;display:flex;align-items:center;gap:8px}
.brand-square{width:26px;height:26px;background:var(--ink)}
.brand-name{font-size:20px;font-weight:800;color:var(--ink);letter-spacing:.3px}
.enquiry{position:absolute;right:0;top:2px;text-align:right}
.enquiry-label{font-size:12px;color:var(--ink);font-weight:600}
.enquiry-phone{font-size:20px;font-weight:700;color:var(--yellow-dark);line-height:1.1}
.slogan{top:58px;height:14px;background:var(--yellow);color:var(--ink);font-size:8.5px;font-weight:600;padding:1px 10px;line-height:12px}

/* navigation */
.nav{top:86px;height:30px;background:var(--nav);display:flex}
.nav a{color:var(--white);text-decoration:none;font-size:10px;font-weight:600;padding:0 15px;line-height:30px}
.nav a.is-active{background:var(--yellow);color:var(--ink)}

/* slider */
.slider{top:124px;height:272px;overflow:hidden}
.slide-photo{position:absolute;inset:0;background:linear-gradient(180deg,#8fb6dc 0%,#c9dbe9 38%,#e9e6dc 55%,#8a9a6a 75%,#4f6a3a 100%)}
.slide-caption{position:absolute;right:0;top:0;width:238px;height:100%;background:rgba(30,30,30,.82);padding:44px 22px 0}
.slide-title{font-size:22px;font-weight:700;color:var(--white)}
.slide-sub{font-size:13px;color:var(--white);margin:2px 0 10px}
.slide-text{font-size:8px;color:#d6d6d6;line-height:1.5}
.btn-learn{display:inline-block;margin-top:14px;background:var(--yellow);color:var(--ink);font-size:8.5px;font-weight:700;padding:6px 14px}
.slider-dots{top:402px;height:8px;display:flex;justify-content:flex-end;gap:5px}
.slider-dots span{width:7px;height:7px;border-radius:50%;background:#c8c8c8}
.slider-dots span.is-active{background:var(--nav)}

/* aktuell */
.aktuell{left:32px;top:424px;width:162px}
.aktuell-card{border:3px solid var(--yellow);background:var(--white)}
.aktuell-head{background:var(--yellow);color:var(--ink);font-size:13px;font-weight:800;padding:4px 8px}
.aktuell-item{padding:7px 8px 6px;border-bottom:1px solid var(--line)}
.aktuell-item h4{font-size:8.5px;color:var(--ink);font-weight:700}
.aktuell-item p{font-size:7px;color:var(--muted)}
.btn-contact{display:block;margin-top:6px;background:var(--ink);color:var(--white);text-align:center;font-size:9.5px;font-weight:700;padding:8px 0;letter-spacing:.3px}

/* welcome */
.welcome{left:214px;top:424px;width:564px}
.section-title{font-size:15px;font-weight:600;color:var(--ink);padding-bottom:6px;border-bottom:1px solid var(--line)}
.welcome-body{display:flex;gap:14px;margin-top:10px}
.floorplan{width:170px;height:118px;flex:none;background:linear-gradient(135deg,#f6f6f6,#dedede);border:1px solid var(--line)}
.welcome-text p{font-size:8px;margin-bottom:7px;line-height:1.5}
.welcome-text .lead{font-weight:700;color:var(--ink)}

/* news */
.news{left:214px;top:740px;width:564px}
.news-grid{display:grid;grid-template-columns:repeat(3,1fr);gap:10px;margin-top:12px}
.news-card{border:1px solid var(--line);background:var(--panel);padding:9px 10px;height:118px}
.news-card h4{font-size:9px;color:var(--ink);font-weight:700;margin-bottom:5px}
.news-card p{font-size:7.5px;line-height:1.5}
.news-card .more{display:block;margin-top:6px;font-size:7.5px;color:var(--yellow-dark);font-weight:700}

/* references */
.references{left:32px;top:768px;width:162px}
.ref-title{font-size:12px;font-weight:800;color:var(--ink);padding-bottom:5px;border-bottom:2px solid var(--yellow)}
.ref-pics{display:flex;gap:6px;margin-top:8px}
.ref-pic{flex:1;height:72px;background:linear-gradient(180deg,#a9c4dc 0%,#e4e0d6 55%,#7f9462 100%)}
.partners{margin-top:18px;display:flex;flex-direction:column;gap:14px;align-items:flex-start}
.badge{background:var(--panel);border:1px solid var(--line)}
.badge-a{width:120px;height:40px;border-radius:4px}
.badge-b{width:150px;height:36px;border-radius:2px}
.badge-c{width:66px;height:66px;border-radius:50%}

/* footer */
.footer{position:absolute;left:0;top:1112px;width:804px;height:88px;background:var(--footer);border-top:3px solid var(--yellow)}
.footer-inner{position:absolute;left:32px;top:8px;width:746px;display:flex;gap:40px}
.footer h5{font-size:9px;font-weight:800;color:var(--ink);margin-bottom:4px;text-transform:uppercase}
.footer ul{list-style:none}
.footer li,.footer address{font-size:7.5px;font-style:normal;line-height:1.45}
.quick{display:flex;gap:30px}
.quick li::before{content:"› ";color:var(--yellow-dark)}
.social li{display:flex;align-items:center;gap:5px;margin-bottom:2px}
.social li i{width:9px;height:9px;border-radius:50%;background:var(--nav);display:inline-block}
.copyright{position:absolute;left:32px;bottom:4px;font-size:7px;color:var(--muted)}
</style>
</head>
<body>

<header class="page header">
  <div class="brand"><span class="brand-square"></span><span class="brand-name">Brunnwald Haus</span></div>
  <div class="enquiry">
    <div class="enquiry-label">Enquiry Now</div>
    <div class="enquiry-phone">0800 412 736</div>
  </div>
</header>
<div class="page slogan">Ihr Partner für individuelle und normierte Wohnbauten</div>

<nav class="page nav">
  <a class="is-active">Home</a><a>Credentials</a><a>Type of Houses</a><a>Current Offers</a><a>Current Buildings</a><a>Services</a><a>About</a><a>Contact</a>
</nav>

<section class="page slider">
  <div class="slide-photo" role="img" aria-label="Photo of a modern white family house with garden"></div>
  <div class="slide-caption">
    <div class="slide-title">Fusce Ultricies</div>
    <div class="slide-sub">Orci ac feugiat suscipit</div>
    <p class="slide-text">Mauris vel lacus vitae felis vestibulum volutpat. Etiam est nunc, venenatis in, tristique eu, imperdiet ac, nisl. Cum sociis natoque penatibus et magnis dis parturient montes, nascetur ridiculus mus.</p>
    <span class="btn-learn">LEARN MORE</span>
  </div>
</section>
<div class="page slider-dots"><span class="is-active"></span><span></span><span></span><span></span></div>

<aside class="page aktuell">
  <div class="aktuell-card">
    <div class="aktuell-head">AKTUELL</div>
    <div class="aktuell-item"><h4>Titel goes here</h4><p>Mauris vel lacus vitae felis vestibulum volutpat. Etiam est nunc.</p></div>
    <div class="aktuell-item"><h4>Titel goes here</h4><p>Mauris vel lacus vitae felis vestibulum volutpat. Etiam est nunc.</p></div>
    <div class="aktuell-item"><h4>Titel goes here</h4><p>Mauris vel lacus vitae felis vestibulum volutpat. Etiam est nunc.</p></div>
    <div class="aktuell-item"><h4>Titel goes here</h4><p>Mauris vel lacus vitae felis vestibulum volutpat. Etiam est nunc.</p></div>
  </div>
  <span class="btn-contact">KONTAKT AUFNEHMEN</span>
</aside>

<section class="page welcome">
  <h2 class="section-title">Welcome to Brunnwald Haus Mainpage</h2>
  <div class="welcome-body">
    <div class="floorplan" role="img" aria-label="Floor plan drawing of a house"></div>
    <div class="welcome-text">
      <p class="lead">Nam cursus. Morbi ut mi. Nullam enim leo, egestas id condimentum.</p>
      <p>Maecenas ut justo et velit placerat molestie. Donec dictum lectus non odio. Cras a ante vitae enim iaculis aliquam. Mauris nunc quam, venenatis nec, euismod sit amet, egestas placerat, est. Pellentesque habitant morbi tristique senectus et netus et malesuada fames.</p>
      <p>Nunc tempus felis vitae urna. Vivamus porttitor, justo eu porta dictum, neque nunc rhoncus nisi, et fringilla ante ipsum nec nulla.</p>
    </div>
  </div>
</section>

<section class="page news">
  <h2 class="section-title">Latest News</h2>
  <div class="news-grid">
    <article class="news-card"><h4>Etiam est nunc</h4><p>Donec scelerisque leo et tortor. Vivamus vitae quam nec orci feugiat suscipit.</p><span class="more">Read more</span></article>
    <article class="news-card"><h4>Aliquam vehicula mi at mauris</h4><p>Donec scelerisque leo et tortor. Vivamus vitae quam nec orci feugiat suscipit.</p><span class="more">Read more</span></article>
    <article class="news-card"><h4>Suspendisse vulputate</h4><p>Donec scelerisque leo et tortor. Vivamus vitae quam nec orci feugiat suscipit.</p><span class="more">Read more</span></article>
    <article class="news-card"><h4>Etiam est nunc</h4><p>Donec scelerisque leo et tortor. Vivamus vitae quam nec orci feugiat suscipit.</p><span class="more">Read more</span></article>
    <article class="news-card"><h4>Aliquam vehicula mi at mauris</h4><p>Donec scelerisque leo et tortor. Vivamus vitae quam nec orci feugiat suscipit.</p><span class="more">Read more</span></article>
    <article class="news-card"><h4>Suspendisse vulputate</h4><p>Donec scelerisque leo et tortor. Vivamus vitae quam nec orci feugiat suscipit.</p><span class="more">Read more</span></article>
  </div>
</section>

<aside class="page references">
  <h3 class="ref-title">REFERENZEN</h3>
  <div class="ref-pics">
    <div class="ref-pic" role="img" aria-label="Reference project house photo"></div>
    <div class="ref-pic" role="img" aria-label="Reference project house photo"></div>
  </div>
  <div class="partners">
    <div class="badge badge-a" role="img" aria-label="KALDORIS partner badge"></div>
    <div class="badge badge-b" role="img" aria-label="VB NULLBAU HELVETIA partner badge"></div>
    <div class="badge badge-c" role="img" aria-label="TELV certificate badge"></div>
  </div>
</aside>

<footer class="footer">
  <div class="footer-inner">
    <div>
      <h5>Quick Links</h5>
      <div class="quick">
        <ul><li>Home</li><li>Credentials</li><li>Type of Houses</li><li>Current Offers</li></ul>
        <ul><li>Current Buildings</li><li>Services</li><li>About</li><li>Contact</li></ul>
      </div>
    </div>
    <div>
      <h5>Contact Info</h5>
      <address>Talackerweg 14<br>CH 8712 Rosshalden<br>Telephon 044 318 52 40<br>Telefax 044 318 52 41<br>info@brunnwaldhaus.ch</address>
    </div>
    <div>
      <h5>Follow Us</h5>
      <ul class="social"><li><i></i>Friendwall</li><li><i></i>Chirpline</li><li><i></i>Workring</li></ul>
    </div>
  </div>
  <div class="copyright">Copyright © 2013 Company Name . All right reserved.</div>
</footer>

</body>
</html>
```